PowerPoint Presentation 10 Slides Needed with custom graphics and possibly animated gifs

I'm creating an educational webinar for professionals. I have 10 slides that need special treatment--effective visuals that really Deliverables10 PowerPoint slides in shared PPT fileWith 10 or more images that communicate the message described in the slides notes for each slide.DeadlineSlides will be used in a PowerPoint presentation Monday, Dec 10.Due date is Friday, Dec 7.Design GuidanceSee attached deck for existing design template/theme (with colors/logo)You should match the designAnimations should be delivered as GIF files that can appear in a slideAnimation can last 4 to 10 seconds.Instead of animations, photos from Framebarrel can be recommended (I have an account and can provide the final file to use).

```html
<!DOCTYPE html>
<html lang="en">
<head>
<meta charset="UTF-8">
<title>How you communicate?</title>
<link rel="stylesheet" href="https://fonts.googleapis.com/css2?family=Barlow:wght@400;500;700&family=Barlow+Condensed:wght@600;700&display=swap">
<style>
  :root {
    --blue: #2b3e91;
    --green: #1f7a3c;
    --text-grey: #4a4a4a;
    --bg-left: #e6e7ea;
    --bg-right: #fbfbfc;
    --ring: #2e8a4a;
  }
  * { margin: 0; padding: 0; box-sizing: border-box; }
  html, body { width: 1200px; height: 674px; overflow: hidden; }
  body { font-family: "Barlow", Arial, sans-serif; }
  .slide {
    position: relative;
    width: 1200px;
    height: 674px;
    background: linear-gradient(100deg, var(--bg-left) 0%, #eeeff1 45%, var(--bg-right) 100%);
    overflow: hidden;
  }
  .series-name {
    position: absolute;
    left: 963px; top: 50px;
    display: flex; align-items: center; gap: 6px;
    font-family: "Barlow", Arial, sans-serif;
    font-weight: 700;
    font-size: 15px;
    line-height: 17px;
    color: var(--blue);
  }
  .series-name .mark {
    width: 7px; height: 7px; border-radius: 50%;
    background: var(--blue); flex: none;
  }
  .brand {
    position: absolute;
    left: 1046px; top: 48px;
    display: flex; align-items: center; gap: 6px;
    color: var(--green);
    font-family: "Barlow", Arial, sans-serif;
    font-weight: 500;
    font-size: 17px;
    line-height: 18px;
  }
  .brand .mark {
    width: 12px; height: 12px; border-radius: 50%;
    background: var(--green); flex: none;
  }
  .title {
    position: absolute;
    left: 0; right: 0; top: 106px;
    text-align: center;
    font-family: "Barlow", Arial, sans-serif;
    font-weight: 700;
    font-size: 36px;
    color: var(--blue);
  }
  .accent-bar {
    position: absolute;
    left: 0; top: 201px;
    width: 33px; height: 281px;
    background: var(--green);
  }
  .option { position: absolute; top: 290px; }
  .option--throw { left: 71px; color: var(--green); }
  .option--offer { left: 902px; color: var(--blue); }
  .option h2 {
    font-family: "Barlow Condensed", Arial, sans-serif;
    font-weight: 700;
    font-size: 44px;
    line-height: 49px;
    text-transform: uppercase;
    white-space: nowrap;
  }
  .option p {
    margin-top: 6px;
    font-size: 17px;
    line-height: 24px;
    color: var(--text-grey);
  }
  .mood {
    position: absolute;
    top: 494px;
    width: 28px; height: 28px;
  }
  .mood--sad { left: 80px; }
  .mood--happy { left: 916px; }
  .photo {
    position: absolute;
    top: 221px;
    width: 292px; height: 292px;
    border-radius: 50%;
    border: 1.5px solid var(--ring);
  }
  .photo--thrown {
    left: 273px;
    background: radial-gradient(circle at 55% 60%, #d9b48c 0%, #ecd8c2 35%, #f8f1ea 65%, #ffffff 90%);
  }
  .photo--offered {
    left: 584px;
    background: radial-gradient(circle at 50% 45%, #f3efe9 0%, #e2d3c0 35%, #8f7764 65%, #5e4a3c 100%);
  }
</style>
</head>
<body>
  <main class="slide">
    <div class="series-name"><span>Start<br>Simple</span><span class="mark"></span></div>
    <div class="brand"><span class="mark"></span><span>Patron<br>Loop</span></div>

    <h1 class="title">How you communicare?</h1>

    <div class="accent-bar"></div>

    <section class="option option--throw">
      <h2>Do you<br>throw it?</h2>
      <p>(Irrespective of the<br>person likes it or not.<br>just keep on throwing)</p>
    </section>
    <svg class="mood mood--sad" viewBox="0 0 28 28" aria-hidden="true">
      <circle cx="14" cy="14" r="12.5" fill="none" stroke="#222" stroke-width="1.6"/>
      <circle cx="10" cy="11" r="1.5" fill="#222"/>
      <circle cx="18" cy="11" r="1.5" fill="#222"/>
      <path d="M9 20 Q14 15.5 19 20" fill="none" stroke="#222" stroke-width="1.6" stroke-linecap="round"/>
    </svg>

    <div class="photo photo--thrown" role="img" aria-label="Photo: chocolate chip cookies flying diagonally across a white background with motion streaks"></div>
    <div class="photo photo--offered" role="img" aria-label="Photo: hands holding a white plate of chocolate-filled cookies over a wooden table"></div>

    <section class="option option--offer">
      <h2>Or do you offer<br>it proudly</h2>
      <p>(and wait for them to<br>take a bite and shower<br>you with praise?)</p>
    </section>
    <svg class="mood mood--happy" viewBox="0 0 28 28" aria-hidden="true">
      <circle cx="14" cy="14" r="12.5" fill="none" stroke="#222" stroke-width="1.6"/>
      <circle cx="10" cy="11" r="1.5" fill="#222"/>
      <circle cx="18" cy="11" r="1.5" fill="#222"/>
      <path d="M9 17 Q14 21.5 19 17" fill="none" stroke="#222" stroke-width="1.6" stroke-linecap="round"/>
    </svg>
  </main>
</body>
</html>
```